Business Card Design Project

This is to go hand in hand with our stationery project.
Target Market(s)
Business Professionals in the Finance, HR and C-Level management arena. They are global companies that run enterprise technology solutions/products.
Mostly Male, mid 30's to 60's.
Industry/Entity Type
Business
Font styles to use
Other font styles liked:
- Calibri
Colors
9bcb3c
000000
1b1b1b
c4c4c4
ffffff
Requirements
Must have
- Logo
Name, title, contact details, address on the front of the card.
ABN and web address need to be on the card, along with our tag line
See | Share | Do
We also require rounded corners and for the card to be landscape please.
Our green is
C98 M0 Y93 K0
Modern, contemporary and must have white space for people to write on.
Nice to have
- Consistent elements with the stationery design.
Should not have
- No 90's waves - We want the feeling of movement but no wavey lines.

```html
<!DOCTYPE html>
<html lang="en">
<head>
<meta charset="utf-8">
<title>Corvane Business Solutions – Business Card</title>
<link href="https://fonts.googleapis.com/css2?family=Open+Sans:wght@400;600;700&display=swap" rel="stylesheet">
<style>
  :root {
    --green: #9bcb3c;
    --black: #000000;
    --charcoal: #1b1b1b;
    --dark-grey: #2a2a2a;
    --mid-grey: #c4c4c4;
    --white: #ffffff;
    --backdrop: #ececec;
    --card-radius: 14px;
  }
  * { box-sizing: border-box; margin: 0; padding: 0; }
  html, body { width: 1200px; height: 914px; overflow: hidden; }
  body {
    background: var(--backdrop);
    font-family: "Open Sans", Calibri, sans-serif;
    display: flex;
    align-items: center;
    justify-content: center;
    gap: 40px;
  }
  .card {
    position: relative;
    width: 540px;
    height: 330px;
    border-radius: var(--card-radius);
    overflow: hidden;
    background: var(--white);
    box-shadow: 0 6px 18px rgba(0,0,0,0.18);
  }

  /* Front */
  .front__header { position: absolute; inset: 0 0 auto 0; height: 142px; background: var(--white); }
  .front__accent { position: absolute; left: 0; right: 0; top: 142px; height: 8px; background: var(--green); }
  .front__body { position: absolute; left: 0; right: 0; top: 150px; bottom: 0; background: var(--charcoal); }

  .brand {
    position: absolute;
    display: flex;
    align-items: center;
    gap: 8px;
    font-weight: 700;
    color: var(--dark-grey);
    letter-spacing: 0.5px;
  }
  .brand__dot { border-radius: 50%; background: var(--green); flex: none; }
  .front .brand { left: 30px; top: 34px; font-size: 34px; }
  .front .brand__dot { width: 16px; height: 16px; }

  .company-name {
    position: absolute;
    left: 262px;
    top: 86px;
    font-size: 19px;
    color: var(--charcoal);
    letter-spacing: 0.6px;
  }

  .person { position: absolute; left: 30px; top: 178px; color: var(--white); }
  .person__name { font-size: 20px; font-weight: 700; letter-spacing: 0.8px; text-transform: uppercase; line-height: 1.1; }
  .person__title { font-size: 12px; font-weight: 600; color: var(--green); margin-top: 1px; }
  .person__address { font-size: 12.5px; color: var(--mid-grey); line-height: 1.45; margin-top: 8px; }

  .divider { position: absolute; left: 280px; top: 200px; width: 1px; height: 90px; background: var(--mid-grey); }

  .contacts { position: absolute; left: 306px; top: 216px; list-style: none; }
  .contacts li {
    display: flex; align-items: center; gap: 10px;
    font-size: 12.5px; color: var(--white); line-height: 1; height: 18px;
  }
  .contacts svg { width: 12px; height: 12px; fill: var(--green); flex: none; }

  /* Back */
  .back { display: flex; flex-direction: column; align-items: center; justify-content: center; }
  .back .brand { position: static; font-size: 44px; }
  .back .brand__dot { width: 20px; height: 20px; }
  .back__descriptor { font-size: 16px; font-weight: 600; color: var(--dark-grey); letter-spacing: 0.5px; margin-top: 2px; }
  .tagline { margin-top: 22px; font-size: 22px; color: var(--black); display: flex; align-items: center; gap: 8px; }
  .tagline__sep { width: 7px; height: 7px; border-radius: 50%; background: var(--green); }
  .abn { margin-top: 6px; font-size: 13px; color: var(--black); letter-spacing: 0.3px; }
</style>
</head>
<body>

  <section class="card front" aria-label="Business card front">
    <div class="front__header"></div>
    <div class="front__accent"></div>
    <div class="front__body"></div>

    <div class="brand"><span>Corvane</span><span class="brand__dot"></span></div>
    <div class="company-name">Corvane Business Solutions</div>

    <div class="person">
      <div class="person__name">Marcus Hale</div>
      <div class="person__title">Managing Director</div>
      <div class="person__address">Level 6, 42 Harbour Lane,<br>Eastwood, NSW 2122</div>
    </div>

    <div class="divider"></div>

    <ul class="contacts">
      <li>
        <svg viewBox="0 0 12 12" aria-hidden="true"><circle cx="6" cy="3.2" r="2.6"/><path d="M1 12c0-3.2 2.2-5 5-5s5 1.8 5 5z"/></svg>
        +61 2 5550 1234
      </li>
      <li>
        <svg viewBox="0 0 12 12" aria-hidden="true"><rect x="3" y="0.5" width="6" height="3"/><rect x="0.5" y="4" width="11" height="5" rx="1"/><rect x="3" y="8" width="6" height="3.5"/></svg>
        +61 2 55501299
      </li>
      <li>
        <svg viewBox="0 0 12 12" aria-hidden="true"><path d="M0.5 2h11v8h-11z M1.5 3l4.5 3.5 4.5-3.5v-0.2h-9z" fill-rule="evenodd"/></svg>
        sales@corvanebiz.com
      </li>
      <li>
        <svg viewBox="0 0 12 12" aria-hidden="true"><path d="M6 0.5a5.5 5.5 0 1 0 0 11 5.5 5.5 0 0 0 0-11zm0 1.3a4.2 4.2 0 0 1 0 8.4 4.2 4.2 0 0 1 0-8.4z" fill-rule="evenodd"/><path d="M3.5 4h5v1.2h-5zM3.5 6.8h5V8h-5zM5.4 2h1.2v8H5.4z"/></svg>
        www.corvanebiz.com
      </li>
    </ul>
  </section>

  <section class="card back" aria-label="Business card back">
    <div class="brand"><span>Corvane</span><span class="brand__dot"></span></div>
    <div class="back__descriptor">Business Solutions</div>
    <div class="tagline">
      <span>Plan</span><span class="tagline__sep"></span><span>Build</span><span class="tagline__sep"></span><span>Grow</span>
    </div>
    <div class="abn">ABN: 12 345678 901</div>
  </section>

</body>
</html>
```